Stationery Design Project

Our company is "Meridian Systems" and we have a product called "lunogrid.com". The product is an online accounting software for businesses. We want to communicate that our software will help business owners to be more efficient and help them track their finances better. Lunogrid.com is basically a simple version of ledgerpal.

"We want a unique and creative design which will surprise our customer."

NAME CARD = LUNOGRID
We want a lunogrid name card NOT MERIDIAN SYSTEMS.

For the content of the name card, please make sure it fit with a long name like the following:

Rudi Wahyo Alias Rudi
Developer Specialist
T: (021) 4827 1036
F: (021) 4827 1037
E: customer.service@mrdn-sys.example

I need you to put it the following information to the name card

"lunogrid"
- moto is "automate your businesses"
- website "www.lunogrid.com"
- lunogrid is a "Web Accounting Software"
- product of "Meridian Systems"

LETTERHEAD, ENVELOPE, FOLDER = MERIDIAN SYSTEMS
Other than name card we wanted you to design for us; letterhead, envelope and folder. In letterhead, envelope and folder it should ONLY contain the following information ("Meridian Systems").
PLEASE BE SURE YOU ARE NOT PUTTING "LUNOGRID LOGO" IN LETTERHEAD, ENVELOPE AND FOLDER.

"Meridian Systems"
Address:
Ruko Graha Pelangi Blok. D No. 18
Jl. Kenanga Raya No. 71
Jakarta
Cempaka, 11470
Indonesia

Web Address: mrdn-sys.example

T: (021) 4827 1036
F: (021) 4827 1037

Target Market(s)

Business Owners, Accountant, Auditor, Tax Consultant

Industry/Entity Type

Accounting

Requirements

```html
<!DOCTYPE html>
<html lang="en">
<head>
<meta charset="utf-8">
<title>Lunogrid Name Card</title>
<link rel="stylesheet" href="https://fonts.googleapis.com/css2?family=Share+Tech+Mono&family=Source+Sans+3:wght@400;600&display=swap">
<style>
  :root {
    --backdrop: #b4b4b4;
    --card: #000000;
    --text-light: #f2f2f2;
    --text-soft: #bdbdbd;
    --brand-grey: #9a9a9a;
    --accent-green: #8cb63c;
    --rule: #6a6a6a;
  }
  * { margin: 0; padding: 0; box-sizing: border-box; }
  html, body {
    width: 1200px; height: 960px; overflow: hidden;
    background: var(--backdrop);
  }
  body { position: relative; font-family: "Source Sans 3", sans-serif; }

  .card { position: absolute; background: var(--card); overflow: hidden; }
  .card--front { left: 268px; top: 58px; width: 698px; height: 412px; }
  .card--back  { left: 271px; top: 509px; width: 693px; height: 409px; }

  .line { position: absolute; line-height: 1; white-space: nowrap; }

  /* Lunogrid brand block */
  .brand-mark {
    position: absolute; left: 50px; top: 34px;
    width: 62px; height: 62px; border-radius: 50%;
    background: var(--accent-green);
  }
  .brand-name {
    left: 124px; top: 42px;
    font-size: 34px; font-weight: 600; letter-spacing: 1px;
    color: var(--brand-grey);
  }
  .brand-motto { left: 119px; top: 94px; font-size: 17px; color: var(--text-light); }
  .brand-web { left: 119px; top: 115px; font-size: 17px; color: var(--text-light); }

  /* Product description block */
  .product-kind {
    left: 47px; top: 148px;
    font-size: 28px; color: var(--text-light);
  }
  .product-maker {
    left: 48px; top: 178px;
    font-family: "Share Tech Mono", monospace;
    font-size: 11px; letter-spacing: 1.2px; color: var(--text-soft);
  }
  .maker-tagline { left: 47px; top: 193px; font-size: 18px; color: var(--text-light); }
  .maker-web { left: 47px; top: 214px; font-size: 18px; color: var(--text-light); }

  .divider {
    position: absolute; left: 41px; top: 247px;
    width: 615px; height: 1px; background: var(--rule);
  }

  .person-name {
    left: 312px; top: 214px;
    font-size: 29px; color: var(--accent-green);
  }
  .person-role {
    left: 313px; top: 256px;
    font-family: "Share Tech Mono", monospace;
    font-size: 16px; letter-spacing: 2.5px; color: var(--text-soft);
  }
  .contact { left: 312px; font-size: 19px; color: var(--text-soft); }
  .contact--phone { top: 297px; }
  .contact--fax { top: 324px; }
  .contact--email { top: 351px; }

  /* Back */
  .back-mark {
    position: absolute; left: 83px; top: 146px;
    width: 106px; height: 106px; border-radius: 50%;
    background: var(--accent-green);
  }
  .back-name {
    left: 208px; top: 164px;
    font-size: 64px; font-weight: 600; letter-spacing: 2px;
    color: var(--brand-grey);
  }
</style>
</head>
<body>
  <section class="card card--front" aria-label="Lunogrid name card front">
    <div class="brand-mark"></div>
    <div class="line brand-name">lunogrid</div>
    <div class="line brand-motto">automate your businesses</div>
    <div class="line brand-web">www.lunogrid.com</div>

    <div class="line product-kind">web accounting software</div>
    <div class="line product-maker">A PRODUCT OF MERIDIAN SYSTEMS</div>
    <div class="line maker-tagline">Digitize Life</div>
    <div class="line maker-web">www.mrdn-sys.example</div>

    <div class="divider"></div>

    <div class="line person-name">Rudi Wahyo Alias Rudi</div>
    <div class="line person-role">DEVELOPER SPECIALIST</div>
    <div class="line contact contact--phone">T: (021) 4827 1036</div>
    <div class="line contact contact--fax">F: (021) 4827 1037</div>
    <div class="line contact contact--email">E: customer.service@mrdn-sys.example</div>
  </section>

  <section class="card card--back" aria-label="Lunogrid name card back">
    <div class="back-mark"></div>
    <div class="line back-name">lunogrid</div>
  </section>
</body>
</html>
```